Financial Advisor Resource Firm needs business card design

Need business card design for company in Omaha NE called Meridale Circle. We provide resources to financial advisors....workshop programs, retirement analysis, and insurance planning. I would like to see designs that use grays, greens, black, and white colors. The final design should communicate 'collaboration' and be simple yet attractive to financial planning clients. I will attached our logo and another picture of a puzzle piece coming together. I would like the incorporate the puzzle picture somehow, maybe on the back somehow, with color or just the gray scale....OR, the picture be the front of the card with 'Meridale' definition on it (see upload) and then company logo, employee name, title, address on the back (see ppt uploaded). The following disclosure needs to be included somewhere- Advisory services offered through Stonebrook Assets, LLC.
Updates

I uploaded a svg and ai file of the logo

Target Market(s)

Financial planning clients and financial advisors....so pretty diverse age range of about 40-70.

Industry/Entity Type

Financial Planning

Contact Information for Business Card

Tobias L. Fenwright, MBA
Founder/President
5287 E. Larkin Road
Suite 230
Omaha, NE 68190
Phone- (402) 555-0147
Cell- (402) 555-0183
Fax- (402) 555-0129
email- tobias@meridaleplan.example
web address- www.meridaleplan.example

Colors
1b1b1b
474747
d3d3d3
ffffff
9bcb3c
abd036

Requirements
Must have
• Must include logo provided, must be 2 sided, and must have disclosure...all of these items listed in project description

```html
<!DOCTYPE html>
<html lang="en">
<head>
<meta charset="utf-8">
<title>Meridale Circle – Business Card</title>
<link rel="stylesheet" href="https://fonts.googleapis.com/css2?family=Tinos:wght@400;700&display=swap">
<style>
  :root {
    --ink: #1b1b1b;
    --graphite: #474747;
    --silver: #d3d3d3;
    --paper: #ffffff;
    --leaf: #9bcb3c;
    --lime: #abd036;
    --backdrop: #e9e9e6;
  }
  * { margin: 0; padding: 0; box-sizing: border-box; }
  html, body {
    width: 1200px;
    height: 1024px;
    overflow: hidden;
    background: var(--backdrop);
    font-family: "Tinos", "Times New Roman", serif;
  }
  .card {
    position: absolute;
    left: 250px;
    width: 700px;
    height: 400px;
    background: var(--paper);
    box-shadow: 0 14px 32px rgba(0,0,0,.25);
    overflow: hidden;
  }
  .card--front { top: 70px; }
  .card--back { top: 554px; background: var(--ink); }

  /* Front */
  .card__top {
    position: absolute;
    inset: 0 0 auto 0;
    height: 220px;
    background: var(--paper);
  }
  .card__band {
    position: absolute;
    left: 0; right: 0;
    top: 220px;
    height: 14px;
    background: var(--leaf);
  }
  .card__bottom {
    position: absolute;
    left: 0; right: 0;
    top: 234px;
    bottom: 0;
    background: linear-gradient(180deg, #141414 0%, var(--ink) 60%, #222 100%);
    color: var(--paper);
  }
  .brand {
    position: absolute;
    left: 43px;
    top: 74px;
    display: flex;
    align-items: center;
    gap: 11px;
  }
  .brand__dot {
    width: 20px; height: 20px;
    border-radius: 50%;
    background: var(--leaf);
  }
  .brand__name {
    font-size: 39px;
    color: var(--ink);
    letter-spacing: 1px;
    text-transform: uppercase;
  }
  .person {
    position: absolute;
    left: 293px;
    top: 140px;
  }
  .person__name {
    font-size: 24px;
    color: var(--ink);
    line-height: 1.15;
  }
  .person__title {
    font-size: 19px;
    color: var(--leaf);
    line-height: 1.25;
  }
  .contact {
    font-size: 18px;
    line-height: 23px;
    list-style: none;
  }
  .phones {
    position: absolute;
    left: 36px;
    top: 26px;
  }
  .phones li, .address {
    display: flex;
    align-items: center;
    gap: 12px;
  }
  .icon { width: 14px; height: 15px; flex: none; fill: var(--leaf); }
  .divider {
    position: absolute;
    left: 325px;
    top: 18px;
    width: 2px;
    height: 35px;
    background: var(--paper);
  }
  .address {
    position: absolute;
    left: 427px;
    top: 20px;
    align-items: flex-start;
  }
  .address .icon { margin-top: 4px; }
  .email {
    position: absolute;
    left: 303px;
    top: 120px;
    font-size: 18px;
  }

  /* Back */
  .puzzle-photo {
    position: absolute;
    inset: 0;
    background: radial-gradient(ellipse at 60% 45%, #8a8a8a 0%, var(--graphite) 45%, #262626 100%);
  }
  .back__band {
    position: absolute;
    left: 0; right: 0;
    bottom: 66px;
    height: 8px;
    background: var(--leaf);
  }
  .back__footer {
    position: absolute;
    left: 0; right: 0;
    bottom: 0;
    height: 66px;
    background: var(--ink);
    color: var(--paper);
    display: flex;
    align-items: center;
    justify-content: space-between;
    padding: 0 36px;
  }
  .back__web { font-size: 18px; color: var(--leaf); }
  .back__disclosure { font-size: 13px; color: var(--silver); }
</style>
</head>
<body>
  <section class="card card--front" aria-label="Meridale Circle business card, front">
    <div class="card__top">
      <div class="brand">
        <span class="brand__dot" aria-hidden="true"></span>
        <span class="brand__name">Meridale Circle</span>
      </div>
      <div class="person">
        <p class="person__name">Tobias L. Fenwright, MBA</p>
        <p class="person__title">Founder/President</p>
      </div>
    </div>
    <div class="card__band"></div>
    <div class="card__bottom">
      <ul class="contact phones">
        <li>
          <svg class="icon" viewBox="0 0 20 22" aria-hidden="true"><rect x="5" y="1" width="10" height="20" rx="2"/><rect x="7" y="4" width="6" height="12" fill="#1b1b1b"/></svg>
          (402) 555-0183
        </li>
        <li>
          <svg class="icon" viewBox="0 0 20 22" aria-hidden="true"><rect x="1" y="6" width="18" height="13" rx="2"/><rect x="5" y="2" width="10" height="6" fill="#1b1b1b" stroke="#9bcb3c" stroke-width="2"/></svg>
          (402) 555-0129
        </li>
        <li>
          <svg class="icon" viewBox="0 0 20 22" aria-hidden="true"><path d="M4 3 L8 3 L9 8 L6.5 9.5 C8 13 10 15 13 16.5 L14.5 14 L19 15 L19 19 C11 20 2 12 3 4 Z"/></svg>
          (402) 555-0147
        </li>
      </ul>
      <span class="divider" aria-hidden="true"></span>
      <div class="contact address">
        <svg class="icon" viewBox="0 0 20 22" aria-hidden="true"><path d="M10 1 C5 1 2 4.5 2 8.5 C2 14 10 21 10 21 C10 21 18 14 18 8.5 C18 4.5 15 1 10 1 Z M10 5.5 A3 3 0 1 1 10 11.5 A3 3 0 1 1 10 5.5 Z"/></svg>
        <p>5287 E. Larkin Road<br>Suite 230<br>Omaha, NE 68190</p>
      </div>
      <p class="email">tobias@meridaleplan.example</p>
    </div>
  </section>

  <section class="card card--back" aria-label="Meridale Circle business card, back">
    <div class="puzzle-photo" role="img" aria-label="Grayscale photograph of two hands joining puzzle pieces"></div>
    <div class="back__band"></div>
    <div class="back__footer">
      <p class="back__web">www.meridaleplan.example</p>
      <p class="back__disclosure">Advisory services offered through Stonebrook Assets, LLC.</p>
    </div>
  </section>
</body>
</html>
```